Thistlewick Superfoods Packaging Design

We are looking for a design for our premium superfoods powders and blends. Packaging dimensions are 21cm x 13cm Kraft packaging (light brown background). This design should be a blueprint for other products that we will be marketing including lions mane mushroom, reishi mushroom, Chaga mushroom, Spirilina, bee pollen, açai powder and the like. The design should be clean but earthy, and the template replicable for other products.

```html
<!DOCTYPE html>
<html lang="en">
<head>
<meta charset="utf-8">
<title>Thistlewick Superfoods – Lions Mane Mushroom</title>
<link rel="stylesheet" href="https://fonts.googleapis.com/css2?family=Cinzel:wght@700&family=Source+Sans+3:wght@400;600;700&display=swap">
<style>
  :root {
    --green-dark: #0a9447;
    --green-mid: #3bb54a;
    --green-light: #7dc242;
    --panel: #000000;
    --gold: #c4a52d;
    --gold-deep: #8f7a22;
    --white: #ffffff;
    --page: #ffffff;
  }
  * { margin: 0; padding: 0; box-sizing: border-box; }
  html, body { width: 743px; height: 1200px; overflow: hidden; background: var(--page); }
  .pack {
    position: relative;
    width: 743px;
    height: 1200px;
    overflow: hidden;
    font-family: "Source Sans 3", sans-serif;
    color: var(--white);
  }
  .pack-shapes { position: absolute; inset: 0; }

  .brand {
    position: absolute;
    left: 76px;
    top: 112px;
    width: 265px;
    text-align: center;
    color: var(--white);
    font-weight: 600;
  }
  .brand-name { font-size: 50px; line-height: 70px; display: block; }
  .brand-rule { height: 3px; background: var(--white); margin-top: 18px; }
  .brand-tag {
    display: block;
    font-size: 18px;
    letter-spacing: 3.5px;
    margin-top: 8px;
    padding-left: 16px;
  }

  .product-title {
    position: absolute;
    left: 68px;
    top: 270px;
    font-family: "Cinzel", serif;
    font-weight: 700;
    font-size: 64px;
    line-height: 73px;
    color: var(--gold);
    letter-spacing: -1px;
  }

  .product-intro {
    position: absolute;
    left: 69px;
    top: 424px;
    width: 570px;
    font-size: 16.3px;
    line-height: 26px;
  }

  .benefits {
    position: absolute;
    left: 67px;
    top: 565px;
    list-style: none;
  }
  .benefits li {
    display: flex;
    align-items: center;
    height: 26.7px;
    font-size: 15.5px;
    font-weight: 600;
  }
  .benefits svg { width: 24px; height: 20px; margin-right: 9px; flex: none; }

  .cert-strip {
    position: absolute;
    left: 67px;
    top: 811px;
    width: 205px;
    height: 56px;
    background: var(--white);
    display: flex;
    align-items: center;
    justify-content: space-around;
    padding: 0 6px;
  }
  .cert-badge { width: 42px; height: 42px; border-radius: 50%; background: var(--green-mid); }
  .cert-badge.is-dark { background: var(--green-dark); }
  .cert-badge.is-square { border-radius: 6px; background: var(--green-light); }

  .net-weight {
    position: absolute;
    left: 63px;
    top: 1105px;
    font-size: 27px;
    font-weight: 700;
    letter-spacing: 0.5px;
  }
  .net-weight small { font-size: 19px; }

  .hero-art { position: absolute; left: 334px; top: 705px; width: 409px; height: 440px; }
</style>
</head>
<body>
<main class="pack">
  <svg class="pack-shapes" width="743" height="1200" viewBox="0 0 743 1200" aria-hidden="true">
    <rect x="34" y="33" width="676" height="1135" fill="var(--green-dark)"/>
    <path d="M377,33 C600,33 709,170 709,300 L709,520 L690,520 C690,260 580,33 377,33 Z" fill="var(--green-light)"/>
    <path d="M377,33 C585,33 709,190 709,360 L709,420 L700,420 C700,230 570,33 377,33 Z" fill="var(--green-mid)"/>
    <path d="M34,33 L377,33 C560,33 709,200 709,400 L709,1168 L305,1168 C150,1168 34,1010 34,835 Z"
          fill="var(--panel)" stroke="var(--gold)" stroke-width="4"/>
    <path d="M34,835 C34,1010 130,1145 305,1168 L34,1168 Z" fill="var(--green-mid)"/>
  </svg>

  <div class="brand">
    <span class="brand-name">Thistlewick</span>
    <div class="brand-rule"></div>
    <span class="brand-tag">SUPERFOODS</span>
  </div>

  <h1 class="product-title">LIONS MANE<br>MUSHROOM</h1>

  <p class="product-intro">Lion’s mane mushrooms, also known as yamabushitake, are large, white, shaggy mushrooms that resemble a lion’s mane as they grow. Lion’s mane mushrooms contain bioactive substances that have beneficial effects on the body, especially the brain, heart and gut.</p>

  <ul class="benefits">
    <li><svg viewBox="0 0 24 20"><path d="M16,4 A8,8 0 1 0 18,11" fill="none" stroke="var(--green-mid)" stroke-width="2.4"/><path d="M6,9 L10,13 L22,2" fill="none" stroke="var(--gold)" stroke-width="2.6"/></svg>Protect Against Dementia</li>
    <li><svg viewBox="0 0 24 20"><path d="M16,4 A8,8 0 1 0 18,11" fill="none" stroke="var(--green-mid)" stroke-width="2.4"/><path d="M6,9 L10,13 L22,2" fill="none" stroke="var(--gold)" stroke-width="2.6"/></svg>Helps Relieve Mild Symptoms of Depression and Anxiety</li>
    <li><svg viewBox="0 0 24 20"><path d="M16,4 A8,8 0 1 0 18,11" fill="none" stroke="var(--green-mid)" stroke-width="2.4"/><path d="M6,9 L10,13 L22,2" fill="none" stroke="var(--gold)" stroke-width="2.6"/></svg>Speed Recovery from Nervous System Injuries</li>
    <li><svg viewBox="0 0 24 20"><path d="M16,4 A8,8 0 1 0 18,11" fill="none" stroke="var(--green-mid)" stroke-width="2.4"/><path d="M6,9 L10,13 L22,2" fill="none" stroke="var(--gold)" stroke-width="2.6"/></svg>Reduces Heart Disease Risk</li>
    <li><svg viewBox="0 0 24 20"><path d="M16,4 A8,8 0 1 0 18,11" fill="none" stroke="var(--green-mid)" stroke-width="2.4"/><path d="M6,9 L10,13 L22,2" fill="none" stroke="var(--gold)" stroke-width="2.6"/></svg>Helps Manage Diabetes Symptoms</li>
    <li><svg viewBox="0 0 24 20"><path d="M16,4 A8,8 0 1 0 18,11" fill="none" stroke="var(--green-mid)" stroke-width="2.4"/><path d="M6,9 L10,13 L22,2" fill="none" stroke="var(--gold)" stroke-width="2.6"/></svg>May Help Fight Cancer</li>
    <li><svg viewBox="0 0 24 20"><path d="M16,4 A8,8 0 1 0 18,11" fill="none" stroke="var(--green-mid)" stroke-width="2.4"/><path d="M6,9 L10,13 L22,2" fill="none" stroke="var(--gold)" stroke-width="2.6"/></svg>Reduces Inflammation and Oxidative Stress</li>
    <li><svg viewBox="0 0 24 20"><path d="M16,4 A8,8 0 1 0 18,11" fill="none" stroke="var(--green-mid)" stroke-width="2.4"/><path d="M6,9 L10,13 L22,2" fill="none" stroke="var(--gold)" stroke-width="2.6"/></svg>Boosts the Immune System</li>
  </ul>

  <div class="cert-strip" aria-label="Certification badges">
    <span class="cert-badge is-dark"></span>
    <span class="cert-badge"></span>
    <span class="cert-badge is-square"></span>
    <span class="cert-badge is-dark"></span>
  </div>

  <svg class="hero-art" viewBox="0 0 409 440" role="img" aria-label="Gold line illustration of a shaggy lion's mane mushroom">
    <defs>
      <linearGradient id="maneTone" x1="0" y1="0" x2="0" y2="1">
        <stop offset="0" stop-color="var(--gold)" stop-opacity="0.85"/>
        <stop offset="1" stop-color="var(--gold-deep)" stop-opacity="0.9"/>
      </linearGradient>
    </defs>
    <path d="M30,420 C0,330 20,220 80,170 C110,90 160,10 230,0 C300,10 360,60 390,150 C409,200 409,300 405,380 C380,430 300,440 200,438 C120,436 60,440 30,420 Z" fill="url(#maneTone)"/>
  </svg>

  <p class="net-weight">250<small>G</small></p>
</main>
</body>
</html>
```